Business Card for a mobile physiotherapy company

I need a layout for a business card for a mobile physiotherapy company.
Slogan is "Mobile Physiotherapy - Your Road To Recovery"
Phone number is 867-555-0142
Email VardenTherapy@postnest.ca (subject to change with website)
Website www.VardenTherapy.ca
My name and credentials: Luke Varden Luke Varden, BSc(kin), MPT, CAFCI, IMS
Information maybe included: Direct Billing, Services including Physiotherapy, IMS, acupuncture
Maybe include facebook and instagram logos
One side with the logo clean and sharp
Other side with details, try not to look too busy, keep everything concise

```html
<!DOCTYPE html>
<html lang="en">
<head>
<meta charset="utf-8">
<title>Varden Therapy – Business Card</title>
<link rel="stylesheet" href="https://fonts.googleapis.com/css2?family=Tinos:wght@400;700&family=PT+Sans:wght@400;700&display=swap">
<style>
  :root {
    --navy: #2c4a78;
    --green: #0f5e4e;
    --ink: #2a2a2a;
    --rule: #c9ccd1;
    --paper: #ffffff;
    --backdrop: #e9eaec;
    --serif: "Tinos", "Times New Roman", serif;
    --sans: "PT Sans", "Helvetica Neue", Arial, sans-serif;
  }
  * { box-sizing: border-box; margin: 0; padding: 0; }
  html, body { width: 1200px; height: 960px; overflow: hidden; }
  body {
    background: var(--backdrop);
    position: relative;
    font-family: var(--sans);
    color: var(--ink);
  }
  .card {
    position: absolute;
    left: 240px;
    width: 720px;
    height: 411px;
    background: var(--paper);
    box-shadow: 0 6px 18px rgba(0,0,0,.12);
    overflow: hidden;
  }
  .card--back { top: 49px; }
  .card--front { top: 500px; }

  /* Back side */
  .brand-name {
    position: absolute;
    left: 0; right: 0; top: 130px;
    display: flex;
    justify-content: center;
    align-items: center;
    gap: 16px;
    font-family: var(--sans);
    font-weight: 700;
    color: var(--navy);
    font-size: 52px;
    line-height: 1;
  }
  .brand-name__square {
    width: 30px; height: 30px;
    background: var(--navy);
    flex: none;
  }
  .socials {
    position: absolute;
    left: 0; right: 0; top: 270px;
    display: flex;
    justify-content: center;
    gap: 70px;
    font-size: 19px;
  }
  .social { display: flex; align-items: center; gap: 10px; }
  .social__square { width: 26px; height: 26px; border-radius: 4px; }
  .social__square--one { background: #4a5a9a; }
  .social__square--two { background: #a8489a; }

  /* Front side */
  .front-name {
    position: absolute;
    left: 40px; top: 100px;
    width: 270px;
    text-align: center;
    font-family: var(--sans);
    font-weight: 700;
    color: var(--navy);
    font-size: 40px;
    line-height: 1.15;
  }
  .divider {
    position: absolute;
    left: 336px; top: 40px;
    width: 1px; height: 250px;
    background: var(--rule);
  }
  .details { position: absolute; left: 362px; top: 44px; }
  .details__name {
    font-family: var(--serif);
    font-weight: 700;
    color: var(--navy);
    font-size: 24px;
    letter-spacing: 1px;
    text-transform: uppercase;
  }
  .details__creds { font-size: 14px; margin-top: 2px; }
  .contact { list-style: none; margin-top: 12px; font-size: 17px; }
  .contact li { display: flex; align-items: center; gap: 8px; line-height: 1.5; }
  .contact svg { width: 15px; height: 15px; flex: none; }
  .services { margin-top: 16px; }
  .services__title { font-weight: 700; color: var(--navy); font-size: 18px; }
  .services__list {
    list-style: none;
    display: grid;
    grid-template-columns: auto auto;
    column-gap: 22px;
    font-size: 17px;
    color: var(--green);
    margin-top: 2px;
  }
  .services__list li::before { content: "• "; }
  .bands { position: absolute; left: 0; bottom: 0; width: 720px; height: 120px; }
  .slogan {
    position: absolute;
    left: 52px; top: 334px;
    font-family: var(--serif);
    font-weight: 700;
    color: var(--navy);
    font-size: 16px;
  }
</style>
</head>
<body>

  <section class="card card--back" aria-label="Card back">
    <div class="brand-name"><span class="brand-name__square"></span>Varden Therapy</div>
    <div class="socials">
      <div class="social"><span class="social__square social__square--one"></span>VardenTherapy</div>
      <div class="social"><span class="social__square social__square--two"></span>@VardenTherapy</div>
    </div>
  </section>

  <section class="card card--front" aria-label="Card front">
    <div class="front-name">Varden<br>Therapy</div>

    <div class="divider"></div>

    <div class="details">
      <h1 class="details__name">Luke Varden</h1>
      <p class="details__creds">BSc(kin), MPT, CAFCI, IMS</p>
      <ul class="contact">
        <li>
          <svg viewBox="0 0 16 16" fill="none" stroke="#2a2a2a" stroke-width="1.4"><circle cx="8" cy="8" r="7"/><path d="M5.5 4.5l1.3 1.8-.8 1c.6 1.2 1.4 2 2.6 2.6l1-.8 1.8 1.3-.9 1.2c-2.9-.5-5.4-3-6-6z" fill="#2a2a2a" stroke="none"/></svg>
          867-555-0142
        </li>
        <li>
          <svg viewBox="0 0 16 16" fill="none" stroke="#2a2a2a" stroke-width="1.4"><circle cx="8" cy="8" r="7"/><rect x="4" y="5.5" width="8" height="5.5"/><path d="M4 5.5l4 3 4-3"/></svg>
          VardenTherapy@postnest.ca
        </li>
        <li>
          <svg viewBox="0 0 16 16" fill="none" stroke="#2a2a2a" stroke-width="1.3"><circle cx="8" cy="8" r="7"/><ellipse cx="8" cy="8" rx="3" ry="7"/><path d="M1 8h14M2.5 4.5h11M2.5 11.5h11"/></svg>
          www.VardenTherapy.ca
        </li>
      </ul>
      <div class="services">
        <h2 class="services__title">Services Including</h2>
        <ul class="services__list">
          <li>Physiotherapy</li>
          <li>Direct Billing</li>
          <li>Ims</li>
          <li>Acupuncture</li>
        </ul>
      </div>
    </div>

    <svg class="bands" viewBox="0 0 720 120" aria-hidden="true">
      <polygon points="0,2 330,2 300,16 0,16" fill="#2c4a78"/>
      <polygon points="300,86 720,86 720,120 0,120 0,104 280,104" fill="#0f5e4e"/>
    </svg>
    <p class="slogan">Mobile Physiotherapy - Your Road To Recovery</p>
  </section>

</body>
</html>
```